Dunmore Roofing

Want a professional looking business card

Industry/Entity Type

Business

Contact Information for Business Card

Paul Dunmore ( Owner) paul@dunmoreroofing-example.com, www.dunmoreroofing-example.com, Adress: 4172 Township road 43 Ferncliff,QC K9X4T2

```html
<!DOCTYPE html>
<html lang="en">
<head>
<meta charset="utf-8">
<title>Dunmore Roofing – Business Card</title>
<link rel="stylesheet" href="https://fonts.googleapis.com/css2?family=Open+Sans:wght@400;600;700&display=swap">
<style>
  :root {
    --backdrop: #5a4f4a;
    --card: #0d0d0e;
    --brand-blue: #1e55a8;
    --silver: #c8c9cb;
    --ink-light: #f2f2f2;
    --divider: #232325;
  }
  html, body {
    margin: 0;
    width: 1200px;
    height: 900px;
    overflow: hidden;
    background: var(--backdrop);
    font-family: "Open Sans", Arial, sans-serif;
  }
  .canvas {
    position: relative;
    width: 1200px;
    height: 900px;
  }
  .card {
    position: absolute;
    top: 300px;
    width: 525px;
    height: 300px;
    background: var(--card);
    box-shadow: 0 6px 18px rgba(0,0,0,0.45);
    overflow: hidden;
  }
  .card--contact { left: 50px; }
  .card--brand { left: 625px; }

  /* Contact side */
  .contact-mark {
    position: absolute;
    left: 36px;
    bottom: 46px;
    display: flex;
    align-items: center;
    gap: 10px;
    color: var(--brand-blue);
    font-weight: 700;
    font-size: 28px;
    letter-spacing: 0.5px;
    white-space: nowrap;
  }
  .contact-mark .mark-square {
    width: 14px;
    height: 14px;
    background: var(--brand-blue);
  }
  .contact-divider {
    position: absolute;
    left: 278px;
    top: 40px;
    width: 1px;
    height: 150px;
    background: var(--divider);
  }
  .contact-details {
    position: absolute;
    left: 292px;
    top: 42px;
    right: 16px;
    color: var(--ink-light);
    font-size: 11px;
    line-height: 1.5;
  }
  .contact-name {
    margin: 0;
    color: var(--brand-blue);
    font-size: 15px;
    font-weight: 400;
    text-transform: uppercase;
    line-height: 1.2;
  }
  .contact-role {
    margin: 0 0 8px 10px;
    font-size: 12px;
  }
  .contact-line {
    display: flex;
    align-items: center;
    gap: 6px;
    margin: 0;
    white-space: nowrap;
  }
  .contact-line svg { flex: none; }
  .contact-address {
    margin: 8px 0 0;
    font-size: 12.5px;
  }

  /* Brand side */
  .brand-lockup {
    position: absolute;
    inset: 0;
    display: flex;
    align-items: center;
    justify-content: center;
    gap: 12px;
    color: var(--silver);
    font-weight: 700;
    font-size: 40px;
    letter-spacing: 1px;
    white-space: nowrap;
  }
  .brand-lockup .mark-square {
    width: 18px;
    height: 18px;
    background: var(--silver);
  }
</style>
</head>
<body>
<main class="canvas">
  <section class="card card--contact" aria-label="Business card, contact side">
    <div class="contact-mark"><span class="mark-square"></span>Dunmore Roofing</div>
    <div class="contact-divider"></div>
    <div class="contact-details">
      <h1 class="contact-name">Paul Dunmore</h1>
      <p class="contact-role">Owner</p>
      <p class="contact-line">
        <svg width="10" height="8" viewBox="0 0 10 8" aria-hidden="true"><rect x="0.5" y="0.5" width="9" height="7" fill="var(--brand-blue)"/><path d="M0.5 0.5 L5 4.5 L9.5 0.5" fill="none" stroke="var(--card)" stroke-width="1"/></svg>
        paul@dunmoreroofing-example.com
      </p>
      <p class="contact-line">
        <svg width="10" height="10" viewBox="0 0 10 10" aria-hidden="true"><circle cx="5" cy="5" r="4.5" fill="var(--brand-blue)"/><path d="M0.5 5 H9.5 M5 0.5 C2.5 3 2.5 7 5 9.5 M5 0.5 C7.5 3 7.5 7 5 9.5" fill="none" stroke="var(--card)" stroke-width="0.7"/></svg>
        www.dunmoreroofing-example.com
      </p>
      <p class="contact-address">4172 Township road 43<br>Ferncliff,QC K9X4T2</p>
    </div>
  </section>

  <section class="card card--brand" aria-label="Business card, brand side">
    <div class="brand-lockup"><span class="mark-square"></span>Dunmore Roofing</div>
  </section>
</main>
</body>
</html>
```